Small legal and financial translation company needs Squarespace website, brochure and logo

Hello,
We are Lumarin Services (www.lumarinservices-example.com), a boutique legal and financial translation company. We offer our services mainly to Spanish customers. Our primary line of business is the translation of financial statements, but we translate a wide variety legal and financial texts.
The project we are offering comprises three parts: a redo of the current website, an informational brochure for potential customer and a logo design. These three parts should provide a consistent image. We would develop content soon.
We are looking for a website that would look like a typical law firm website, nothing too fancy. Right now, it is in English, Spanish and French, although the new site need only be in English and Spanish. There must be good toggling between the English and Spanish versions. There would be no need for tie-ins to social media and it would not contain a blog. Basically, a static site. We aren't interesting in driving traffic to the site or SEO, as we will contact nearly all potential customers beforehand. The website must be built in Squarespace to enable a smooth transition. The content would be similar to the current page, we'll be working on the exact content, but a rough draft is attached.
The brochure will be some three pages and would introduce the company to potential customers, using similar images as the website and the logo to be designed.
The only specifications for the logo is, as the website and brochure, it convey a sense of security and trust.
Feel free to ask with any questions as this is the first time we have used this platform.
Thank you!
Updates

I've added a more or less final version for the text in the brochure and updated the brief. Added Wednesday, June 10, 2015

Target Market(s)

Spanish law firms, auditors, accountants, banks, investment firms

Industry/Entity Type

Finance

Logo Text

Lumarin Services

Number of Pages Required

5+ page

Font styles to use
Serif

Requirements
Must have
• The website must be built in Squarespace and have a good option to toggle between English and Spanish versions.
• Brochure must be in both English and Spanish, I'm attaching a rough draft of the information that it will probably have. This should give an idea about what to include and the spacing. I will update it to include the final information.
Nice to have
• Would be nice to have some quality finance- and legal-related images
Should not have
• Vibrant colours

```html
<!DOCTYPE html>
<html lang="en">
<head>
<meta charset="utf-8">
<title>Lumarin Services – Brochure Pages 3 and 4</title>
<link rel="stylesheet" href="https://fonts.googleapis.com/css2?family=Cinzel:wght@400&family=Crimson+Text:wght@400;700&family=Open+Sans:wght@400&display=swap">
<style>
  :root {
    --board: #c8c8c8;
    --label: #555555;
    --burgundy: #7a0010;
    --ink: #111111;
    --body-ink: #333333;
    --muted-ink: #6a6a6a;
    --paper: #ffffff;
    --night: #000000;
    --panel: #e6e6e8;
  }
  * { box-sizing: border-box; margin: 0; padding: 0; }
  html, body { width: 1200px; height: 1066px; overflow: hidden; }
  body { background: var(--board); position: relative; font-family: "Crimson Text", Georgia, serif; }

  .page-label {
    position: absolute; top: 46px; width: 200px; text-align: center;
    font-family: "Open Sans", Arial, sans-serif; font-size: 28px; color: var(--label);
  }
  .page-label--left { left: 237px; }
  .page-label--right { left: 783px; }

  .spread {
    position: absolute; left: 54px; top: 108px; width: 1100px; height: 849px;
    box-shadow: 0 0 22px rgba(0,0,0,0.35);
  }
  .page { position: absolute; top: 0; width: 550px; height: 849px; overflow: hidden; }
  .page--expertise { left: 0; background: var(--paper); }
  .page--comparison { left: 550px; background: var(--night); }

  .hero-photo {
    position: absolute; left: 0; top: 0; width: 550px; height: 300px;
    background: linear-gradient(180deg, #d9d9d9 0%, #e8e8e8 45%, #f6f6f6 80%, #ffffff 100%),
                radial-gradient(ellipse at 35% 45%, #9a9a9a 0%, transparent 60%);
    background-blend-mode: multiply;
  }

  .section-title {
    position: absolute; left: 26px; top: 286px;
    font-family: "Cinzel", "Times New Roman", serif; font-size: 24px;
    color: var(--burgundy); letter-spacing: 1px;
  }

  .expertise-item { position: absolute; left: 28px; width: 500px; }
  .expertise-item__number {
    position: absolute; left: 0; top: 0; width: 54px; height: 54px;
    border: 1.5px solid var(--ink); border-radius: 50%;
    display: flex; align-items: center; justify-content: center;
    font-size: 30px; color: var(--ink); line-height: 1;
  }
  .expertise-item__title {
    position: absolute; left: 66px; top: -25px; font-weight: 700; font-size: 15.5px; color: var(--ink); white-space: nowrap;
  }
  .expertise-item__text {
    position: absolute; left: 66px; top: 1px; width: 430px;
    font-size: 12.6px; line-height: 15.5px; color: var(--body-ink); text-align: justify;
  }
  .expertise-item--one { top: 342px; }
  .expertise-item--two { top: 477px; }
  .expertise-item--three { top: 604px; }
  .expertise-item--two .expertise-item__title { top: -20px; left: 65px; }
  .expertise-item--two .expertise-item__text { top: 4px; }
  .expertise-item--three .expertise-item__title { top: -24px; }

  .footer-shape { position: absolute; left: 0; bottom: 0; width: 550px; height: 102px; }
  .footer-url {
    position: absolute; left: 23px; top: 805px;
    font-size: 19px; color: var(--paper); white-space: nowrap;
  }

  .comparison-title {
    position: absolute; left: 0; top: 33px; width: 550px; text-align: center;
    font-family: "Cinzel", "Times New Roman", serif; font-size: 23px; line-height: 28px;
    color: var(--paper); letter-spacing: 1.5px;
  }

  .comparison-column { position: absolute; top: 156px; width: 250px; height: 533px; background: var(--panel); }
  .comparison-column--agency { left: 21px; }
  .comparison-column--provider { left: 281px; }
  .comparison-column__header {
    height: 58px; background: var(--burgundy); color: var(--paper);
    font-size: 20px; padding: 16px 0 0 36px; white-space: nowrap;
  }
  .comparison-column--provider .comparison-column__header { padding-left: 33px; }
  .comparison-column__text {
    position: absolute; left: 12px; width: 223px;
    font-size: 12.3px; line-height: 15.5px; color: var(--muted-ink); text-align: justify;
  }
  .comparison-column__text:nth-of-type(1) { top: 78px; }
  .comparison-column__text:nth-of-type(2) { top: 231px; }
  .comparison-column__text:nth-of-type(3) { top: 384px; }
</style>
</head>
<body>
  <div class="page-label page-label--left">Page 3</div>
  <div class="page-label page-label--right">Page 4</div>

  <main class="spread">
    <section class="page page--expertise">
      <div class="hero-photo" role="img" aria-label="Black and white photo of a hand signing a document with a pen beside a keyboard and coffee cup"></div>
      <h2 class="section-title">Areas of expertise</h2>

      <article class="expertise-item expertise-item--one">
        <span class="expertise-item__number">1</span>
        <h3 class="expertise-item__title">Duis autem vel eum iriure dolor</h3>
        <p class="expertise-item__text">Lorem ipsum dolor sit amet, consectetuer adipiscing elit, sed diam nonummy nibh euismod tincidunt ut laoreet dolore magna aliquam erat volutpat. Ut wisi enim ad minim veniam, quis nostrud exerci tation ullamcorper suscipit lobortis nisl ut aliquip ex ea commodo consequat.</p>
      </article>
      <article class="expertise-item expertise-item--two">
        <span class="expertise-item__number">2</span>
        <h3 class="expertise-item__title">Duis autem vel eum iriure dolor</h3>
        <p class="expertise-item__text">Lorem ipsum dolor sit amet, consectetuer adipiscing elit, sed diam nonummy nibh euismod tincidunt ut laoreet dolore magna aliquam erat volutpat. Ut wisi enim ad minim veniam, quis nostrud exerci tation ullamcorper suscipit lobortis nisl ut aliquip ex ea commodo consequat.</p>
      </article>
      <article class="expertise-item expertise-item--three">
        <span class="expertise-item__number">3</span>
        <h3 class="expertise-item__title">Duis autem vel eum iriure dolor</h3>
        <p class="expertise-item__text">Lorem ipsum dolor sit amet, consectetuer adipiscing elit, sed diam nonummy nibh euismod tincidunt ut laoreet dolore magna aliquam erat volutpat. Ut wisi enim ad minim veniam, quis nostrud exerci tation ullamcorper suscipit lobortis nisl ut aliquip ex ea commodo consequat.</p>
      </article>

      <svg class="footer-shape" viewBox="0 0 550 102" aria-hidden="true">
        <polygon points="0,0 550,102 0,102" fill="var(--burgundy)"/>
        <polygon points="281,52 550,0 550,102" fill="var(--night)"/>
      </svg>
      <div class="footer-url">www.lumarinservices-example.com</div>
    </section>

    <section class="page page--comparison">
      <h2 class="comparison-title">Differences between working<br>with a translation agency<br>and a translation provider</h2>

      <div class="comparison-column comparison-column--agency">
        <h3 class="comparison-column__header">Translation Agency</h3>
        <p class="comparison-column__text">Lorem ipsum dolor sit amet, consectetuer adipiscing elit, sed diam nonummy nibh euismod tincidunt ut laoreet dolore magna aliquam erat volutpat. Ut wisi enim ad minim veniam, quis nostrud exerci tation ullamcorper suscipit lobortis nisl ut aliquip ex ea commodo consequat.</p>
        <p class="comparison-column__text">Lorem ipsum dolor sit amet, consectetuer adipiscing elit, sed diam nonummy nibh euismod tincidunt ut laoreet dolore magna aliquam erat volutpat. Ut wisi enim ad minim veniam, quis nostrud exerci tation ullamcorper suscipit lobortis nisl ut aliquip ex ea commodo consequat.</p>
        <p class="comparison-column__text">Lorem ipsum dolor sit amet, consectetuer adipiscing elit, sed diam nonummy nibh euismod tincidunt ut laoreet dolore magna aliquam erat volutpat. Ut wisi enim ad minim veniam, quis nostrud exerci tation ullamcorper suscipit lobortis nisl ut aliquip ex ea commodo consequat.</p>
      </div>
      <div class="comparison-column comparison-column--provider">
        <h3 class="comparison-column__header">Translation Provider</h3>
        <p class="comparison-column__text">Lorem ipsum dolor sit amet, consectetuer adipiscing elit, sed diam nonummy nibh euismod tincidunt ut laoreet dolore magna aliquam erat volutpat. Ut wisi enim ad minim veniam, quis nostrud exerci tation ullamcorper suscipit lobortis nisl ut aliquip ex ea commodo consequat.</p>
        <p class="comparison-column__text">Lorem ipsum dolor sit amet, consectetuer adipiscing elit, sed diam nonummy nibh euismod tincidunt ut laoreet dolore magna aliquam erat volutpat. Ut wisi enim ad minim veniam, quis nostrud exerci tation ullamcorper suscipit lobortis nisl ut aliquip ex ea commodo consequat.</p>
        <p class="comparison-column__text">Lorem ipsum dolor sit amet, consectetuer adipiscing elit, sed diam nonummy nibh euismod tincidunt ut laoreet dolore magna aliquam erat volutpat. Ut wisi enim ad minim veniam, quis nostrud exerci tation ullamcorper suscipit lobortis nisl ut aliquip ex ea commodo consequat.</p>
      </div>

      <svg class="footer-shape" viewBox="0 0 550 102" aria-hidden="true">
        <polygon points="0,0 550,102 0,102" fill="var(--burgundy)"/>
        <line x1="0" y1="0" x2="550" y2="102" stroke="var(--paper)" stroke-width="1.2"/>
      </svg>
      <div class="footer-url">www.lumarinservices-example.com</div>
    </section>
  </main>
</body>
</html>
```